Business Card Design

Online clothing womens clothing store, I sell my clothing online and at the markets.

i would like the attached picture on the front of the card and the contact information on the back.

Industry/Entity Type

Business

Contact Information for Business Card

Marlow Thread
Karen Whitfield
(Instagram symbol) _marlow_thread_
(Facebook symbol) www.fakebookexample.com/marlowthreadau/

W : www.marlowthread.example.au
E : info@marlowthread.example.au
P : 0498716204

```html
<!DOCTYPE html>
<html lang="en">
<head>
<meta charset="utf-8">
<title>Marlow Thread – Business Card</title>
<link rel="stylesheet" href="https://fonts.googleapis.com/css2?family=Open+Sans:wght@300;400&display=swap">
<style>
  :root {
    --backdrop: #1b1b1d;
    --card-black: #0c0c0d;
    --ink-dark: #161616;
    --ink-light: #ffffff;
    --accent-blue: #4d68c4;
    --photo-light: #e9e6e1;
    --photo-warm: #c9ad98;
    --photo-wood: #a8916f;
    --photo-grass: #4f6a32;
  }
  * { box-sizing: border-box; margin: 0; padding: 0; }
  html, body {
    width: 1200px; height: 922px; overflow: hidden;
    background: var(--backdrop);
    font-family: "Open Sans", Arial, sans-serif;
  }
  .sheet {
    width: 1200px; height: 922px;
    display: flex; flex-direction: column; align-items: center; justify-content: center;
    gap: 40px;
  }
  .card {
    position: relative;
    width: 700px; height: 400px;
    border-radius: 16px;
    overflow: hidden;
  }

  /* Front */
  .card-front .photo {
    position: absolute; inset: 0;
    background: linear-gradient(180deg,
      var(--photo-light) 0%, #dcd8d0 30%, var(--photo-warm) 55%,
      var(--photo-wood) 72%, var(--photo-grass) 100%);
  }
  .card-front .logo-band {
    position: absolute; left: 0; right: 0; top: 160px; height: 120px;
    background: rgba(255, 255, 255, 0.28);
  }
  .card-front .wordmark {
    position: absolute; left: 0; right: 0; top: 190px;
    text-align: center;
    font-weight: 300; font-size: 52px; letter-spacing: 12px;
    color: var(--ink-dark);
    text-transform: uppercase;
  }

  /* Back */
  .card-back { background: var(--card-black); }
  .card-back .photo-panel { position: absolute; inset: 0; }
  .card-back .details {
    position: absolute; right: 34px; top: 50px;
    width: 380px;
    text-align: right;
    color: var(--ink-light);
  }
  .card-back .wordmark {
    font-weight: 300; font-size: 30px; letter-spacing: 7px;
    text-transform: uppercase;
  }
  .card-back .holder-name {
    margin-top: 30px;
    font-weight: 400; font-size: 34px;
  }
  .contact-list {
    list-style: none;
    margin-top: 50px;
  }
  .contact-list li {
    display: flex; justify-content: flex-end; align-items: center; gap: 14px;
    font-size: 16px; line-height: 30px;
  }
  .contact-icon {
    width: 20px; height: 20px; flex: none;
    background: var(--ink-light);
    border-radius: 2px;
    display: flex; align-items: center; justify-content: center;
  }
  .contact-icon svg { width: 14px; height: 14px; }
  .contact-icon.plain { background: transparent; border: 2px solid var(--ink-light); }
</style>
</head>
<body>
<main class="sheet">

  <section class="card card-front" aria-label="Card front">
    <div class="photo" role="img" aria-label="Photo of two women in boho clothing sitting on a wooden porch"></div>
    <div class="logo-band"></div>
    <div class="wordmark">Marlow Thread</div>
  </section>

  <section class="card card-back" aria-label="Card back">
    <svg class="photo-panel" width="700" height="400" viewBox="0 0 700 400" role="img" aria-label="Photo of two women in boho clothing sitting on a wooden porch">
      <defs>
        <linearGradient id="photoTone" x1="0" y1="0" x2="0" y2="1">
          <stop offset="0" stop-color="#e9e6e1"/>
          <stop offset="0.35" stop-color="#d6cfc4"/>
          <stop offset="0.6" stop-color="#c0a48c"/>
          <stop offset="0.78" stop-color="#9a8463"/>
          <stop offset="1" stop-color="#4f6a32"/>
        </linearGradient>
      </defs>
      <polygon points="0,0 330,0 400,200 330,400 0,400" fill="url(#photoTone)"/>
      <polyline points="330,0 400,200 330,400" fill="none" stroke="#4d68c4" stroke-width="4"/>
    </svg>

    <div class="details">
      <div class="wordmark">Marlow Thread</div>
      <div class="holder-name">Karen Whitfield</div>
      <ul class="contact-list">
        <li>0498716204
          <span class="contact-icon"><svg viewBox="0 0 16 16"><path d="M4 1.5l2.5 3-1.5 1.5c.8 1.8 2.2 3.2 4 4l1.5-1.5 3 2.5-1.5 2.5C7 13 3 9 1.5 3z" fill="#0c0c0d"/></svg></span></li>
        <li>info@marlowthread.example.au
          <span class="contact-icon"><svg viewBox="0 0 16 16"><rect x="1.5" y="3.5" width="13" height="9" fill="none" stroke="#0c0c0d" stroke-width="1.5"/><path d="M1.5 3.5l6.5 5 6.5-5" fill="none" stroke="#0c0c0d" stroke-width="1.5"/></svg></span></li>
        <li>www.marlowthread.example.au
          <span class="contact-icon"><svg viewBox="0 0 16 16"><circle cx="8" cy="8" r="6" fill="none" stroke="#0c0c0d" stroke-width="1.5"/><path d="M2 8h12M8 2c-2.5 3-2.5 9 0 12M8 2c2.5 3 2.5 9 0 12" fill="none" stroke="#0c0c0d" stroke-width="1.2"/></svg></span></li>
        <li>marlow_thread
          <span class="contact-icon plain"></span></li>
        <li>www.fakebookexample.com
          <span class="contact-icon plain"></span></li>
      </ul>
    </div>
  </section>

</main>
</body>
</html>
```